Quorva - corporate Business Card

We need a good look and innovative business card for a new start up company based in Los Angeles called "Quorva". We are in a payment business, including payment card, app, and ewallet. We are expert in online payment and Card not present (CNP) transaction.
We need an innovative, modern business card.

Our logo font is Aero Matics

Target Market(s)

Startup - Bank - Online Payment - Card Manufacturing

Industry/Entity Type

Startup

Contact Information for Business Card

phone: 555 014 7396 - Address: 4172 Marlowe blvd, Alderwick, NV 89012

Requirements
Must have
• Message: innovative, professional, expert, high tech, trust, online payment expert, security
Nice to have
• no comment
Should not have
• no Comment

```html
<!DOCTYPE html>
<html lang="en">
<head>
<meta charset="utf-8">
<title>Quorva Business Card</title>
<link href="https://fonts.googleapis.com/css2?family=Exo+2:wght@400;500;700&display=swap" rel="stylesheet">
<style>
  :root {
    --backdrop: #5b5b5b;
    --card-front: #fbfbfb;
    --card-back: #f7f7f7;
    --brand-red: #b81e2e;
    --brand-red-bright: #c42434;
    --ink: #1c1c1c;
  }
  html, body {
    margin: 0;
    padding: 0;
    width: 1200px;
    height: 900px;
    overflow: hidden;
    background: var(--backdrop);
    font-family: "Exo 2", sans-serif;
  }
  .stage {
    position: relative;
    width: 1200px;
    height: 900px;
  }
  .card {
    position: absolute;
    top: 192px;
    height: 491px;
    border-radius: 14px;
  }
  .card--front {
    left: 295px;
    width: 301px;
    background: var(--card-front);
    border-radius: 0 14px 14px 0;
  }
  .card--back {
    left: 621px;
    width: 305px;
    background: var(--card-back);
  }
  .brand {
    position: absolute;
    left: 28px;
    top: 87px;
    display: flex;
    align-items: center;
    gap: 8px;
  }
  .brand__dot {
    width: 76px;
    height: 76px;
    border-radius: 50%;
    background: var(--brand-red);
  }
  .brand__name {
    font-size: 50px;
    font-weight: 500;
    color: var(--brand-red);
    letter-spacing: 1px;
    line-height: 1;
    padding-bottom: 8px;
  }
  .contact {
    position: absolute;
    left: 0;
    right: 0;
    top: 264px;
    text-align: center;
    color: var(--ink);
  }
  .contact__name {
    font-size: 26px;
    font-weight: 700;
    color: var(--brand-red);
    line-height: 1;
  }
  .contact__role {
    font-size: 15px;
    margin-top: 4px;
  }
  .contact__rule {
    width: 140px;
    height: 1px;
    margin: 8px auto;
    background: linear-gradient(90deg, transparent, var(--brand-red), transparent);
  }
  .contact__line {
    font-size: 14px;
    line-height: 20px;
  }
  .contact__address {
    font-size: 14px;
    line-height: 18px;
    margin-top: 6px;
  }
  .back-mark {
    position: absolute;
    left: 74px;
    top: 167px;
    width: 156px;
    height: 156px;
    border-radius: 50%;
    background: var(--brand-red-bright);
    box-shadow: 0 0 0 1px #3a0a10;
  }
</style>
</head>
<body>
<main class="stage">
  <section class="card card--front">
    <div class="brand">
      <span class="brand__dot"></span>
      <span class="brand__name">quorva</span>
    </div>
    <div class="contact">
      <div class="contact__name">Dana Whitlow</div>
      <div class="contact__role">Director</div>
      <div class="contact__rule"></div>
      <div class="contact__line">555 014 7396</div>
      <div class="contact__line">www.quorva.com</div>
      <div class="contact__rule"></div>
      <div class="contact__address">4172 Marlowe blvd,<br>Alderwick, NV 89012</div>
    </div>
  </section>
  <section class="card card--back">
    <div class="back-mark"></div>
  </section>
</main>
</body>
</html>
```